Lawn Sign Design – Brisqel

We need a clean, eye-catching 18" x 24" lawn sign for Brisqel that effectively communicates our core message while maintaining strong brand consistency.

Key Elements to Include:
Tagline (Main Focus): Upgrade Your Roof Without Replacing It
Website: www.trybrisqel.com
Phone Number: (888) BRISQEL-GO
TWQB License Number: 4480512
Brisqel Logo & Branding: Ensure the logo, corporate colors, and custom font are used consistently to align with our existing branding.

Design Guidelines:
Simple & High-Impact: The tagline should be the most prominent element on the sign, drawing immediate attention.
Easy Readability: Use a bold, clean design with high contrast for quick readability from a distance.
Balanced Layout: Place supporting details (website, phone number, and TWQB number) in a visually clear but secondary position to the tagline.
Professional & Modern: The sign should reflect credibility and innovation in the roofing industry.

Deliverables:
High-resolution print-ready files (CMYK)
A digital proof for review before finalizing
The final design should make a strong impression with minimal text, ensuring that anyone passing by can instantly grasp what we offer.

I am including our custom font. To get an hexagon in our name, simply type the $ after the 'O" Please use this font for anything you type.

```html
<!DOCTYPE html>
<html lang="en">
<head>
<meta charset="utf-8">
<title>Brisqel Lawn Sign</title>
<link rel="stylesheet" href="https://fonts.googleapis.com/css2?family=Nunito:wght@800;900&display=swap">
<style>
  :root {
    --brand-blue: #1a529a;
    --shingle-light: #4464a0;
    --shingle-dark: #2f4d82;
    --shadow-navy: #12305a;
    --white: #ffffff;
  }
  * { margin: 0; padding: 0; box-sizing: border-box; }
  html, body { width: 900px; height: 1200px; overflow: hidden; background: var(--white); }
  .sign {
    position: relative;
    width: 900px;
    height: 1200px;
    overflow: hidden;
    font-family: "Nunito", "Arial Rounded MT Bold", sans-serif;
    background: var(--brand-blue);
  }
  .roof-photo {
    position: absolute;
    inset: 0 0 auto 0;
    height: 291px;
    background: linear-gradient(170deg, var(--shingle-light), var(--shingle-dark));
  }
  .brand-name {
    position: absolute;
    left: 0; right: 0;
    top: 88px;
    text-align: center;
    font-weight: 900;
    font-size: 112px;
    line-height: 1;
    letter-spacing: 2px;
    color: var(--white);
  }
  .divider {
    position: absolute;
    left: 0;
    width: 900px;
    height: 24px;
  }
  .divider--top { top: 278px; }
  .divider--bottom { top: 876px; }
  .tagline {
    position: absolute;
    left: 50px;
    top: 337px;
    font-weight: 900;
    font-size: 114px;
    line-height: 128px;
    letter-spacing: -2px;
    color: var(--white);
    text-shadow: 4px 4px 0 var(--shadow-navy);
    white-space: nowrap;
  }
  .tagline__line { display: block; height: 128px; }
  .tagline__line--second { position: relative; }
  .tagline__highlight {
    position: absolute;
    left: 396px;
    top: 0;
    width: 454px;
    height: 126px;
    background: var(--white);
    padding-left: 32px;
    color: var(--brand-blue);
    text-shadow: 4px 4px 0 var(--shadow-navy);
    line-height: 128px;
  }
  .contact {
    position: absolute;
    left: 172px;
    top: 918px;
  }
  .contact__row {
    display: flex;
    align-items: center;
    height: 74px;
    margin-bottom: 18px;
  }
  .contact__icon { width: 73px; height: 73px; flex: none; }
  .contact__text {
    margin-left: 25px;
    font-weight: 800;
    font-size: 50px;
    color: var(--white);
    text-shadow: 3px 3px 0 var(--shadow-navy);
    white-space: nowrap;
  }
  .contact__text--phone { font-weight: 900; font-size: 47px; }
  .license {
    position: absolute;
    left: 0; right: 0; bottom: 0;
    height: 83px;
    background: var(--white);
    display: flex;
    align-items: center;
    justify-content: center;
    font-weight: 900;
    font-size: 49px;
    color: var(--brand-blue);
  }
</style>
</head>
<body>
<main class="sign">
  <div class="roof-photo" role="img" aria-label="Close-up photo of blue asphalt roof shingles"></div>
  <div class="brand-name">BRISQEL</div>

  <svg class="divider divider--top" viewBox="0 0 900 24" aria-hidden="true">
    <path d="M0 11.5 L442 10.5 L900 11.5 L900 13.5 L442 13.5 L0 12.5 Z" fill="#ffffff"/>
    <circle cx="442" cy="12" r="9.5" fill="#1a529a" stroke="#ffffff" stroke-width="3"/>
  </svg>

  <h1 class="tagline">
    <span class="tagline__line">UPGRADE</span>
    <span class="tagline__line tagline__line--second">YOUR <span class="tagline__highlight">ROOF</span></span>
    <span class="tagline__line">WITHOUT</span>
    <span class="tagline__line">REPLACING IT</span>
  </h1>

  <svg class="divider divider--bottom" viewBox="0 0 900 24" aria-hidden="true">
    <path d="M0 11.5 L442 10.5 L900 11.5 L900 13.5 L442 13.5 L0 12.5 Z" fill="#ffffff"/>
    <circle cx="442" cy="12" r="9.5" fill="#1a529a" stroke="#ffffff" stroke-width="3"/>
  </svg>

  <div class="contact">
    <div class="contact__row">
      <svg class="contact__icon" viewBox="0 0 72 72" aria-hidden="true">
        <circle cx="36" cy="36" r="36" fill="#ffffff"/>
        <g fill="none" stroke="#1a529a" stroke-width="4">
          <circle cx="36" cy="36" r="24"/>
          <ellipse cx="36" cy="36" rx="11" ry="24"/>
          <line x1="36" y1="12" x2="36" y2="60"/>
          <line x1="12" y1="36" x2="60" y2="36"/>
          <line x1="15" y1="25" x2="57" y2="25"/>
          <line x1="15" y1="47" x2="57" y2="47"/>
        </g>
      </svg>
      <span class="contact__text">www.trybrisqel.com</span>
    </div>
    <div class="contact__row">
      <svg class="contact__icon" viewBox="0 0 72 72" aria-hidden="true">
        <circle cx="36" cy="36" r="36" fill="#ffffff"/>
        <path d="M23 18c3-2 6-1 7 2l3 7c1 2 0 4-2 5l-3 2c2 5 6 9 11 12l2-3c1-2 3-2 5-1l7 3c3 1 3 4 2 7l-2 3c-2 3-6 4-10 2-11-5-19-13-23-24-1-4 0-8 3-10z" fill="#1a529a"/>
        <g fill="none" stroke="#1a529a" stroke-width="3.5" stroke-linecap="round">
          <path d="M40 24a9 9 0 0 1 8 8"/>
          <path d="M41 16a17 17 0 0 1 15 15"/>
        </g>
      </svg>
      <span class="contact__text contact__text--phone">(888) BRISQEL-GO</span>
    </div>
  </div>

  <footer class="license">TWQB License Number: 4480512</footer>
</main>
</body>
</html>
```